Design a compelling Tarnwove Business Card that will drive people to my site

I want a business card that I can give to people—less to tell them who I am and more to direct them to my website. My website is a portal for Pelmor Aquatics Officials and a place for people who want to become Pelmor Aquatics Officials.
I am uploading my official company logo as well as a business card mockup that I did on my own. Please feel free to completely stray from this design.
I've included a screen recording of the homepage of my website as well.
Target Market(s)
Pelmor Aquatics Officials and people who desire to become one
Contact Information for Business Card
website url
Look and feel
Each slider illustrates characteristics of the customer's brand and the style your logo design should communicate.

```html
<!DOCTYPE html>
<html lang="en">
<head>
<meta charset="UTF-8">
<title>Tarnwove Business Card</title>
<link href="https://fonts.googleapis.com/css2?family=Poppins:wght@400;500;600;700&display=swap" rel="stylesheet">
<style>
  :root {
    --backdrop: #2a2a2d;
    --card-blue: #3952a5;
    --soft-blue: #93a8dc;
    --name-blue: #a9b9ea;
    --deep-blue: #3a50a8;
    --edge-blue: #4c66c0;
    --white: #ffffff;
  }
  * { margin: 0; padding: 0; box-sizing: border-box; }
  html, body {
    width: 1186px; height: 1200px; overflow: hidden;
    background: var(--backdrop);
    font-family: "Poppins", sans-serif;
  }
  .sheet {
    width: 1186px; height: 1200px;
    display: flex; flex-direction: column; align-items: center;
    justify-content: center; gap: 38px;
  }
  .card {
    position: relative; width: 960px; height: 541px;
    background: var(--card-blue); overflow: hidden;
  }
  /* Front */
  .front .wordmark {
    position: absolute; right: 62px; top: 118px;
    font-size: 84px; font-weight: 600; letter-spacing: -2px;
    color: var(--white); line-height: 1;
  }
  .front .identity { position: absolute; left: 62px; top: 264px; }
  .front .name {
    font-size: 32px; font-weight: 700; color: var(--name-blue); line-height: 1.2;
  }
  .front .role { font-size: 25px; font-weight: 400; color: var(--white); line-height: 1.3; }
  .front .divider {
    position: absolute; left: 62px; top: 366px; width: 834px; height: 2px;
    background: var(--soft-blue);
  }
  .front .divider::before {
    content: ""; position: absolute; left: 0; top: -1px;
    width: 306px; height: 4px; background: var(--white);
  }
  .front .contacts {
    position: absolute; left: 62px; top: 386px; list-style: none;
  }
  .front .contacts li {
    display: flex; align-items: center; gap: 6px;
    font-size: 25px; color: var(--white); line-height: 35px;
  }
  .front .contacts svg { width: 17px; height: 17px; fill: var(--name-blue); }
  /* Back */
  .back .wordmark {
    position: absolute; left: 0; right: 0; top: 42px; text-align: center;
    font-size: 116px; font-weight: 600; letter-spacing: -3px;
    color: var(--white); line-height: 1;
  }
  .back .wave { position: absolute; left: 0; top: 0; width: 960px; height: 541px; }
  .back .tagline {
    position: absolute; right: 64px; bottom: 42px;
    font-size: 27px; font-weight: 500; color: var(--deep-blue);
  }
</style>
</head>
<body>
<main class="sheet">
  <section class="card front">
    <div class="wordmark">tarnwove</div>
    <div class="identity">
      <p class="name">Daniel Ferrow</p>
      <p class="role">CEO &amp; Founder</p>
    </div>
    <div class="divider"></div>
    <ul class="contacts">
      <li><svg viewBox="0 0 16 16"><path d="M3 2h3l1.5 3.5-2 1.3a8 8 0 0 0 3.7 3.7l1.3-2L14 10v3a1 1 0 0 1-1 1A11 11 0 0 1 2 3a1 1 0 0 1 1-1z"/></svg>(555) 210-4471</li>
      <li><svg viewBox="0 0 16 16"><path d="M1 4h14v9H1zM1.5 4.5 8 9l6.5-4.5" stroke="#3952a5" stroke-width="1"/></svg>dan@tarnwove.com</li>
      <li><svg viewBox="0 0 16 16"><circle cx="8" cy="8" r="7"/><path d="M1 8h14M8 1c-3 3.5-3 10.5 0 14M8 1c3 3.5 3 10.5 0 14" stroke="#3952a5" stroke-width="1" fill="none"/></svg>www.tarnwove.com</li>
    </ul>
  </section>

  <section class="card back">
    <div class="wordmark">tarnwove</div>
    <svg class="wave" viewBox="0 0 960 541" aria-hidden="true">
      <path d="M0 250 C 20 420, 160 470, 330 470 C 520 470, 700 400, 960 400 L 960 541 L 0 541 Z" fill="var(--soft-blue)"/>
      <path d="M0 250 C 20 420, 160 470, 330 470 C 520 470, 700 400, 960 400" fill="none" stroke="var(--edge-blue)" stroke-width="6"/>
    </svg>
    <p class="tagline">Your Deckside Officials’ Gateway</p>
  </section>
</main>
</body>
</html>
```